Bring me business with this creative business card

Design my new business card. I am looking for something different with an impact. People will take a look at this card & they will 1- see how different & creative I am, 2-understand what I do 3- Call me to meet me!

I make videos with a message, testimonials. I am dynamic, fun, creative & human. My new website is in construction but in the meantime you can check this old one: brightpath.ca & another one Tidebloom.com & tidebloom facebook page.
I make videos. sometimes with a cameraman, sometimes with my phone. As an ex Public Relations agent, the message is the most important thing for me. I want to make my clients shine! When they start with me they often remind me of a lamb, when I finish coaching them they are powerful like LIONS! That's why I need a powerful business card!

Target Market(s)

Entrepreneurs, solo entrepreneurs, small & medium companies & start ups. People i will meet while networking. People that need videos on their website & social Networks to get attention, to be visible. men & women. From 35 to 49 years old.
I am an ex Public relations agent. I used to send clients in traditional medias, now with videos they have more chances to be seen on google the new media. I do videos of the president, his team, his loyal clients saying how great the company is & expert videos like series so people can be seen for example every 1 st of every month with a short 2 minute video. Also with my 20 years in marketing & communications I can coach & give tips to anybody who needs it.
Target: anybody who would like my old website brightpath.ca & I also have another website but it will be off line soon: tidebloom.com could give you ideas.

Industry/Entity Type

Communications

Contact Information for Business Card

I am in Montreal,So the business cards have to be the usual size like we have in Montreal: 9 cm x 5 cm
Details:My text: Mathilde Tessier Communication coach/Chief Lion. "Creating Videos as unique as you" off: 514-555-0147 cell: 514-555-0183. tidebloom.com
mathilde@tidebloom.com logo facebook, youtube, instagram

Colors
f37122

Requirements
Must have
• Dynamic, happy. Orange. Be creative in the look but NOT the shape of the card. Easy to read. Big enough to read.
Should not have
• No funny shapes: no round, no square, just the usual. I love creative but NOT on shape.

```html
<!DOCTYPE html>
<html lang="en">
<head>
<meta charset="utf-8">
<title>Tidebloom Business Card</title>
<link rel="stylesheet" href="https://fonts.googleapis.com/css2?family=Roboto:wght@400;500;700&display=swap">
<style>
  :root {
    --backdrop: #d9d5cf;
    --card-surface: #eef0ef;
    --name-red: #d9381e;
    --title-orange: #e8711c;
    --ink: #2f2f2f;
    --icon-orange: #e0552a;
    --brand-red: #c9401d;
    --art-light: #f6d62a;
    --art-mid: #f39a1e;
    --art-deep: #e5431f;
  }
  * { box-sizing: border-box; margin: 0; padding: 0; }
  html, body {
    width: 1200px;
    height: 969px;
    overflow: hidden;
    background: var(--backdrop);
    font-family: "Roboto", Arial, sans-serif;
  }
  .business-card {
    position: absolute;
    left: 100px;
    top: 206px;
    width: 1000px;
    height: 556px;
    border-radius: 32px;
    background: var(--card-surface);
    box-shadow: 0 12px 40px rgba(0,0,0,0.12);
    overflow: hidden;
  }
  .mascot-art {
    position: absolute;
    left: 26px;
    top: 43px;
    width: 438px;
    height: 512px;
    clip-path: polygon(12% 0, 88% 0, 100% 18%, 100% 70%, 70% 100%, 30% 100%, 0 70%, 0 18%);
    background: radial-gradient(ellipse at 50% 50%, var(--art-light) 0%, var(--art-mid) 45%, var(--art-deep) 100%);
  }
  .identity {
    position: absolute;
    right: 64px;
    top: 94px;
    text-align: right;
  }
  .person-name {
    font-size: 31px;
    font-weight: 700;
    color: var(--name-red);
    letter-spacing: 0.5px;
  }
  .person-role {
    font-size: 25px;
    font-weight: 500;
    color: var(--title-orange);
    line-height: 31px;
    margin-top: 14px;
  }
  .contact-list {
    position: absolute;
    right: 64px;
    top: 240px;
    list-style: none;
    text-align: right;
  }
  .contact-item {
    display: flex;
    justify-content: flex-end;
    align-items: center;
    gap: 14px;
    font-size: 22px;
    color: var(--ink);
    height: 32px;
  }
  .contact-icon {
    width: 20px;
    height: 20px;
    flex: none;
  }
  .brand-name {
    position: absolute;
    left: 560px;
    width: 390px;
    top: 398px;
    text-align: center;
    font-size: 56px;
    font-weight: 500;
    color: var(--brand-red);
    letter-spacing: 3px;
    line-height: 64px;
  }
</style>
</head>
<body>
  <div class="business-card">
    <div class="mascot-art" role="img" aria-label="Geometric low-poly lion head illustration in yellow, orange and red"></div>

    <div class="identity">
      <p class="person-name">MATHILDE T.</p>
      <p class="person-role">COMMUNICATION COACH<br>CHIEF LION</p>
    </div>

    <ul class="contact-list">
      <li class="contact-item">514-555-0147
        <svg class="contact-icon" viewBox="0 0 24 24" fill="var(--icon-orange)"><path d="M6.6 10.8c1.4 2.8 3.8 5.1 6.6 6.6l2.2-2.2c.3-.3.7-.4 1-.2 1.1.4 2.300.6 3.6.6.6 0 1 .4 1 1V20c0 .6-.4 1-1 1C10.6 21 3 13.4 3 4c0-.6.4-1 1-1h3.5c.6 0 1 .4 1 1 0 1.3.2 2.5.6 3.6.1.3 0 .7-.2 1z"/></svg>
      </li>
      <li class="contact-item">514-555-0183
        <svg class="contact-icon" viewBox="0 0 24 24" fill="none" stroke="var(--icon-orange)" stroke-width="2"><rect x="7" y="2" width="10" height="20" rx="2"/><line x1="11" y1="18" x2="13" y2="18"/></svg>
      </li>
      <li class="contact-item">mathilde@tidebloom.com
        <svg class="contact-icon" viewBox="0 0 24 24"><rect x="2" y="5" width="20" height="14" rx="1" fill="var(--icon-orange)"/><path d="M3 6l9 7 9-7" fill="none" stroke="var(--card-surface)" stroke-width="1.6"/></svg>
      </li>
      <li class="contact-item">www.tidebloom.com
        <svg class="contact-icon" viewBox="0 0 24 24" fill="none" stroke="var(--icon-orange)" stroke-width="2"><circle cx="12" cy="12" r="9" fill="var(--icon-orange)"/><path d="M3 12h18M12 3c3 3 3 15 0 18M12 3c-3 3-3 15 0 18" stroke="var(--card-surface)" stroke-width="1.4"/></svg>
      </li>
    </ul>

    <p class="brand-name">TIDEBLOOM</p>
  </div>
</body>
</html>
```